Design 4 pages for an event discovery website

This is a contest for the design of 4 pages for an events discovery website. The feature is part of the new sign-up process.

Please see the attached document for a full scope, mockups and the parent category icons.

Target Market(s)

18-35 Australian event goers

Industry/Entity Type

Events

Number of Pages Required

4 page

```html
<!DOCTYPE html>
<html lang="en">
<head>
<meta charset="utf-8">
<title>Gigloom – Sign Up</title>
<link rel="stylesheet" href="https://fonts.googleapis.com/css2?family=Open+Sans:wght@400;600&display=swap">
<style>
:root{
  --rust:#b5400f;
  --header-bg:rgba(70,45,25,.72);
  --field-bg:rgba(150,140,135,.45);
  --panel-bg:rgba(40,30,25,.35);
  --white:#ffffff;
  --error:#ef5a55;
  --signup-btn:#8a7a68;
  --search-bg:rgba(200,170,130,.55);
  --search-btn:#3a2c20;
  --hero-top:#9a6532;
  --hero-mid:#5e3c24;
  --hero-bottom:#1c120c;
}
*{box-sizing:border-box;margin:0;padding:0}
html,body{width:1200px;height:831px;overflow:hidden}
body{font-family:"Open Sans",Arial,sans-serif;color:var(--white);position:relative;background:var(--hero-bottom)}
.hero-photo{position:absolute;left:0;top:0;width:1200px;height:746px;
  background:linear-gradient(180deg,var(--hero-top) 0%,var(--hero-mid) 45%,var(--hero-bottom) 100%)}
.site-header{position:absolute;left:0;top:0;width:1200px;height:90px;background:var(--header-bg)}
.brand{position:absolute;left:60px;top:22px;font-size:34px;font-weight:600;line-height:44px}
.nav-link{position:absolute;left:218px;top:37px;font-size:15px;font-weight:600}
.search{position:absolute;left:557px;top:30px;width:288px;height:32px;display:flex}
.search-field{flex:1;background:var(--search-bg)}
.search-btn{width:28px;background:var(--search-btn);display:flex;align-items:center;justify-content:center}
.btn-top{position:absolute;top:30px;width:132px;height:32px;font-size:15px;font-weight:600;
  display:flex;align-items:center;justify-content:center}
.btn-signup{left:861px;background:var(--signup-btn);color:#1a1410}
.btn-login{left:1001px;background:var(--rust)}
.signup-panel{position:absolute;left:88px;top:181px;width:325px;height:491px;background:var(--panel-bg)}
.signup-title{position:absolute;left:112px;top:190px;font-size:33px;font-weight:400}
.field{position:absolute;left:112px;width:278px;height:37px;background:var(--field-bg);
  font-size:15.5px;padding-left:14px;line-height:37px}
.field-select svg{position:absolute;right:12px;top:13px}
.btn-submit{position:absolute;left:112px;top:581px;width:278px;height:62px;background:var(--rust);
  font-size:22px;display:flex;align-items:center;justify-content:center}
.error{position:absolute;left:412px;font-size:13px;color:var(--error)}
.benefits-title{position:absolute;left:555px;top:262px;font-size:33px;font-weight:400}
.benefits{list-style:none;position:absolute;left:561px;top:344px}
.benefits li{font-size:14.6px;height:35.4px;display:flex;align-items:center;gap:12px;white-space:nowrap}
.dots{position:absolute;left:561px;top:717px;display:flex;gap:12px}
.dot{width:10px;height:10px;border:1.5px solid var(--white);border-radius:50%}
.dot.active{background:var(--white)}
.site-footer{position:absolute;left:0;top:746px;width:1200px;height:85px;background:var(--rust)}
.legal{position:absolute;left:60px;top:30px;font-size:17.5px}
.legal u{text-underline-offset:3px}
.social{position:absolute;left:1066px;top:34px;display:flex;gap:14px}
.social span{width:16px;height:16px;border-radius:50%;background:var(--white)}
</style>
</head>
<body>
<div class="hero-photo" role="img" aria-label="Blurred photo of a crowd at a live concert"></div>

<header class="site-header">
  <div class="brand">Gigloom</div>
  <div class="nav-link">Find Events</div>
  <div class="search">
    <div class="search-field"></div>
    <div class="search-btn">
      <svg width="13" height="13" viewBox="0 0 13 13" fill="none" stroke="#fff" stroke-width="1.6"><circle cx="5.5" cy="5.5" r="4"/><path d="M8.5 8.5l3.5 3.5"/></svg>
    </div>
  </div>
  <div class="btn-top btn-signup">SIGNUP</div>
  <div class="btn-top btn-login">LOGIN</div>
</header>

<div class="signup-panel"></div>
<h1 class="signup-title">Sign Up</h1>
<div class="field" style="top:255px">User Name</div>
<div class="field" style="top:302px">Email Address</div>
<div class="field" style="top:349px">Password</div>
<div class="field" style="top:395px">Confirm Password</div>
<div class="field" style="top:441px">First Name</div>
<div class="field" style="top:487px">Last Name</div>
<div class="field field-select" style="top:534px">Date Of Birth
  <svg width="14" height="9" viewBox="0 0 14 9" fill="none" stroke="#fff" stroke-width="2"><path d="M1 1l6 6 6-6"/></svg>
</div>
<div class="btn-submit">SIGN UP</div>
<div class="error" style="top:268px">* Wrong Username</div>
<div class="error" style="top:315px">* Wrong Mailid</div>

<h2 class="benefits-title">Benefits</h2>
<ul class="benefits">
  <li><svg width="12" height="12" viewBox="0 0 12 12" fill="none" stroke="#fff" stroke-width="1.3"><path d="M1 6l3 5 7-10"/></svg>Get personalised event recommendations</li>
  <li><svg width="12" height="12" viewBox="0 0 12 12" fill="none" stroke="#fff" stroke-width="1.3"><path d="M1 6l3 5 7-10"/></svg>Get notified about your favourite events - never miss out again</li>
  <li><svg width="12" height="12" viewBox="0 0 12 12" fill="none" stroke="#fff" stroke-width="1.3"><path d="M1 6l3 5 7-10"/></svg>Follow all your favourite artists, musicians, teams and players in one place</li>
  <li><svg width="12" height="12" viewBox="0 0 12 12" fill="none" stroke="#fff" stroke-width="1.3"><path d="M1 6l3 5 7-10"/></svg>Follow your favourite local venues to know everything happening there</li>
  <li><svg width="12" height="12" viewBox="0 0 12 12" fill="none" stroke="#fff" stroke-width="1.3"><path d="M1 6l3 5 7-10"/></svg>Get curated news and feature content on your favourite artists (coming soon)</li>
  <li><svg width="12" height="12" viewBox="0 0 12 12" fill="none" stroke="#fff" stroke-width="1.3"><path d="M1 6l3 5 7-10"/></svg>Invite your mates to events via Friendnet (FN sign-up only)</li>
</ul>
<div class="dots"><span class="dot"></span><span class="dot active"></span><span class="dot"></span><span class="dot"></span></div>

<footer class="site-footer">
  <p class="legal">©2015 yoursite - Terms of Service - Privacy - <u>Contact</u></p>
  <div class="social" aria-label="Social links"><span></span><span></span><span></span></div>
</footer>
</body>
</html>
```